Fun, Clean Business Card For Family Focused Travel Agency

I need a business card using specific colors and fonts as in the uploaded files. Ideally, I would like a large image of the logo on the back and all the contact info on the front. Maybe the stars/dots somewhere in a flowy form.

I do want it the contact information to be clear and easy to read. I don't want it to look too busy. Maybe even a bit minimalist.

I plan or ordering the ROUNDED CORNER business cards from Cardwell Press, so please consider that in your design.

Target Market(s)

Families with children, couples, groups of friends

Contact Information for Business Card

Marla Quint, Owner
Marla@TumbleTrips.example
Cell Phone Number 555-218-4603
Office Phone Number 555-647-1925
Specializing in Glimmerland destinations, Pelican Bay Fun Park, Cruises and All-Inclusive Vacations.

Nice but not required:
www.TumbleTrips.example
Facebook, Instagram, Twitter icons with username: TumbleTrips

Font styles to use
Sans Serif

Requirements
Must have
• Please try to use the colors from the logo as much as possible. I understand lighter shades/colors may be needed for some things.
Should not have
• NO SERIF FONTS. That is really the only thing I do not want at all

```html
<!DOCTYPE html>
<html lang="en">
<head>
<meta charset="utf-8">
<title>TumbleTrips Business Card</title>
<link href="https://fonts.googleapis.com/css2?family=Open+Sans:wght@400;600;700&family=Kaushan+Script&display=swap" rel="stylesheet">
<style>
  :root {
    --navy: #12162b;
    --ink: #161b36;
    --teal: #17b194;
    --orange: #f0892b;
    --yellow: #e2b62a;
    --green: #7cbf3c;
    --blue: #2a9fd8;
    --paper: #ffffff;
    --stage: #3a3a3d;
  }
  * { box-sizing: border-box; margin: 0; padding: 0; }
  html, body { width: 1200px; height: 880px; overflow: hidden; }
  body {
    background: var(--stage);
    font-family: "Open Sans", Arial, sans-serif;
    position: relative;
  }
  .card {
    position: absolute;
    width: 640px;
    height: 366px;
    border-radius: 26px;
    overflow: hidden;
  }
  .card-back { left: 80px; top: 60px; background: var(--navy); color: var(--paper); }
  .card-front { left: 480px; top: 454px; background: var(--paper); color: var(--ink); }

  /* back */
  .back-logo { position: absolute; left: 150px; top: 90px; display: flex; align-items: center; gap: 22px; }
  .back-mark {
    width: 96px; height: 110px; border-radius: 48px 48px 40px 40px;
    background: linear-gradient(160deg, var(--paper) 0 35%, var(--teal) 55%, var(--orange) 75%, var(--blue));
  }
  .wordmark { font-weight: 700; font-size: 54px; letter-spacing: -0.5px; line-height: 1; }
  .card-back .wordmark { color: var(--paper); }
  .tagline { position: absolute; left: 0; right: 0; top: 236px; text-align: center; font-size: 15px; line-height: 1.5; }
  .tagline strong { font-weight: 700; }

  /* front */
  .ship-art {
    position: absolute; left: 0; top: 110px; width: 300px; height: 256px;
    border-radius: 0 140px 0 0;
    background: linear-gradient(170deg, var(--ink) 0 38%, var(--teal) 52%, var(--green) 64%, var(--orange) 74%, var(--yellow) 84%, var(--blue));
  }
  .dots { position: absolute; left: 0; top: 0; }
  .front-wordmark { position: absolute; left: 330px; top: 44px; color: var(--ink); font-size: 50px; }
  .rule { position: absolute; left: 330px; top: 114px; width: 280px; height: 2px; background: var(--teal); }
  .person { position: absolute; left: 330px; top: 128px; }
  .person-name { font-family: "Kaushan Script", cursive; font-size: 28px; color: var(--ink); line-height: 1.1; }
  .person-role { font-size: 15px; color: var(--teal); }
  .contact-list { position: absolute; left: 330px; top: 204px; list-style: none; }
  .contact-list li { display: flex; align-items: center; gap: 8px; font-size: 15px; line-height: 24px; }
  .contact-icon { width: 18px; height: 18px; flex: none; }
  .social { position: absolute; left: 330px; top: 290px; display: flex; gap: 6px; }
  .social span { width: 26px; height: 26px; border-radius: 3px; background: var(--blue); }
  .handle-band {
    position: absolute; left: 432px; top: 290px; right: 0; height: 26px;
    background: var(--teal); color: var(--paper);
    font-weight: 700; font-size: 14px; line-height: 26px; padding-left: 40px;
  }
</style>
</head>
<body>

<section class="card card-back" aria-label="Card back">
  <div class="back-logo">
    <div class="back-mark" role="img" aria-label="Logo illustration: sailing ship on colourful waves"></div>
    <div class="wordmark">TumbleTrips</div>
  </div>
  <p class="tagline"><strong>Specializing in</strong> Glimmerland destinations<br>Pelican Bay Fun Park | Cruises and All-Inclusive Vacations.</p>
</section>

<section class="card card-front" aria-label="Card front">
  <svg class="dots" width="320" height="120" viewBox="0 0 320 120" aria-hidden="true">
    <circle cx="150" cy="90" r="5" fill="var(--teal)"/>
    <circle cx="240" cy="50" r="5" fill="var(--teal)"/>
    <circle cx="200" cy="100" r="4" fill="var(--yellow)"/>
    <circle cx="300" cy="110" r="5" fill="var(--blue)"/>
    <circle cx="60" cy="160" r="4" fill="var(--orange)"/>
  </svg>
  <div class="ship-art" role="img" aria-label="Large illustration of a sailing ship with teal sails on multicoloured waves"></div>

  <div class="wordmark front-wordmark">TumbleTrips</div>
  <div class="rule"></div>
  <div class="person">
    <div class="person-name">Marla Quint</div>
    <div class="person-role">Owner</div>
  </div>
  <ul class="contact-list">
    <li>
      <svg class="contact-icon" viewBox="0 0 18 18" aria-hidden="true"><circle cx="9" cy="9" r="9" fill="var(--teal)"/><rect x="6" y="4" width="6" height="10" rx="1" fill="none" stroke="#fff" stroke-width="1.4"/></svg>
      555-218-4603
    </li>
    <li>
      <svg class="contact-icon" viewBox="0 0 18 18" aria-hidden="true"><circle cx="9" cy="9" r="9" fill="var(--teal)"/><path d="M5 7c0-2 8-2 8 0v1h-2V7H7v1H5z M6 9h6v4H6z" fill="#fff"/></svg>
      555-647-1925
    </li>
    <li>
      <svg class="contact-icon" viewBox="0 0 18 18" aria-hidden="true"><circle cx="9" cy="9" r="9" fill="var(--teal)"/><rect x="4.5" y="6" width="9" height="6" fill="none" stroke="#fff" stroke-width="1.3"/><path d="M4.5 6l4.5 3.5L13.5 6" fill="none" stroke="#fff" stroke-width="1.3"/></svg>
      Marla@TumbleTrips.example
    </li>
  </ul>
  <div class="social" aria-label="Social profiles">
    <span></span><span></span><span></span>
  </div>
  <div class="handle-band">TumbleTrips</div>
</section>

</body>
</html>
```